Harborlight Amusement Collective (HAC)

We need a business card design for Harborlight Amusement Collective. Modern and sleek looking, with all critical information. Open to single or double sided designs, if double sided info needs to be all on one side. The main Logo is Harborlight Amusement collective and must be on the card. The other three logos are for the brands that fall under the group, they might be good on the back.

Industry/Entity Type

Business

```html
<!DOCTYPE html>
<html lang="en">
<head>
<meta charset="utf-8">
<title>Harborlight Amusement Collective – Business Card</title>
<link rel="stylesheet" href="https://fonts.googleapis.com/css2?family=Open+Sans:wght@400;600;700&display=swap">
<style>
  :root {
    --stage: #2e2e2e;
    --card: #ffffff;
    --blue: #1f4f9c;
    --green: #8a9e37;
    --ink: #2a2a2a;
    --font: "Open Sans", Arial, sans-serif;
  }
  * { box-sizing: border-box; margin: 0; padding: 0; }
  html, body { width: 1200px; height: 900px; overflow: hidden; }
  body { background: var(--stage); font-family: var(--font); position: relative; }

  .card { position: absolute; top: 306px; height: 271px; background: var(--card); overflow: hidden; }
  .card--front { left: 149px; width: 439px; }
  .card--back { left: 608px; width: 441px; }

  /* front */
  .tab-blue { position: absolute; left: 0; top: 26px; width: 16px; height: 37px; background: var(--blue); clip-path: polygon(0 0, 100% 0, 100% 100%, 0 100%); }
  .tab-green { position: absolute; left: 12px; top: 26px; width: 17px; height: 37px; background: var(--green); clip-path: polygon(0 0, 100% 0, 100% 100%, 30% 100%); }
  .person { position: absolute; left: 36px; top: 29px; }
  .person__name { font-size: 15px; font-weight: 600; color: var(--blue); letter-spacing: .2px; line-height: 20px; }
  .person__name span { color: var(--green); }
  .person__role { font-size: 11.5px; color: var(--ink); line-height: 15px; }

  .brand { position: absolute; right: 26px; top: 102px; text-align: right; }
  .brand__name { font-size: 16px; font-weight: 600; color: var(--blue); line-height: 21px; letter-spacing: .3px; text-transform: uppercase; }
  .brand__mark { display: inline-block; width: 12px; height: 12px; background: var(--green); margin-bottom: 8px; }

  .contact { position: absolute; left: 28px; top: 180px; list-style: none; }
  .contact li { display: flex; align-items: center; height: 16px; font-size: 12px; color: var(--ink); }
  .contact svg { width: 10px; height: 10px; margin-right: 6px; fill: var(--blue); }

  .address { position: absolute; right: 26px; top: 210px; text-align: right; font-size: 12px; line-height: 16px; color: var(--ink); }

  .band-blue { position: absolute; left: 0; bottom: 0; width: 218px; height: 13px; background: var(--blue); clip-path: polygon(0 0, 100% 0, 95% 100%, 0 100%); }
  .band-green { position: absolute; right: 0; bottom: 0; width: 230px; height: 19px; background: var(--green); clip-path: polygon(8% 0, 100% 0, 100% 100%, 0 100%); }

  /* back */
  .back__field { position: absolute; left: 0; top: 0; width: 100%; height: 200px;
    background: linear-gradient(62deg, #7f9b3c 4%, #2d5a98 38%, #24559f 58%, #4f7b6a 80%, #86a035 100%);
    display: flex; align-items: center; justify-content: center; }
  .back__name { font-size: 44px; font-weight: 700; color: #ffffff; letter-spacing: 4px; }
  .brands { position: absolute; left: 0; top: 200px; width: 100%; height: 71px; display: flex; align-items: center; justify-content: space-around; padding: 0 20px; }
  .brands__item { display: flex; align-items: center; font-size: 13.5px; font-weight: 700; }
  .brands__item i { display: inline-block; width: 14px; height: 14px; border-radius: 50%; margin-right: 5px; }
  .brands__item--a { color: #1c1c1c; } .brands__item--a i { background: #1c1c1c; }
  .brands__item--b { color: var(--blue); } .brands__item--b i { background: var(--green); border-radius: 0; }
  .brands__item--c { color: var(--blue); font-size: 17px; font-weight: 600; } .brands__item--c i { background: var(--blue); width: 20px; height: 20px; }
</style>
</head>
<body>
  <section class="card card--front">
    <div class="tab-blue"></div>
    <div class="tab-green"></div>
    <div class="person">
      <p class="person__name">ELLIOT <span>MARSH</span></p>
      <p class="person__role">Managing Director</p>
    </div>

    <div class="brand">
      <span class="brand__mark"></span>
      <p class="brand__name">Harborlight Amusement<br>Collective</p>
    </div>

    <ul class="contact">
      <li><svg viewBox="0 0 10 10"><rect x="2.5" y="0" width="5" height="10" rx="1"/><rect x="3.5" y="1.2" width="3" height="6.5" fill="#fff"/></svg>044-987 650 312</li>
      <li><svg viewBox="0 0 10 10"><path d="M1 3 Q5 0 9 3 L8 5 L6.5 4 L6.5 3 L3.5 3 L3.5 4 L2 5 Z M2 6 H8 V9 H2 Z"/></svg>044-987 650 312</li>
      <li><svg viewBox="0 0 10 10"><rect x="0" y="2" width="10" height="6.5"/><path d="M0 2 L5 6 L10 2" stroke="#fff" stroke-width="1" fill="none"/></svg>hello@harborlight.example</li>
      <li><svg viewBox="0 0 10 10"><circle cx="5" cy="5" r="5"/><path d="M2 3 Q4 4 3 6 M6 2 Q8 4 6 8" stroke="#fff" stroke-width="1" fill="none"/></svg>www.harborlight.example</li>
    </ul>

    <p class="address">48 Wharfside Lane<br>Port Avalen, 204816.</p>

    <div class="band-blue"></div>
    <div class="band-green"></div>
  </section>

  <section class="card card--back">
    <div class="back__field">
      <p class="back__name">HAC</p>
    </div>
    <div class="brands">
      <span class="brands__item brands__item--a"><i></i>Bleacher Hospitality</span>
      <span class="brands__item brands__item--b"><i></i>Tidal Tickets</span>
      <span class="brands__item brands__item--c"><i></i>passmark</span>
    </div>
  </section>
</body>
</html>
```